Brimlow Plumbing Solutions

This is for my new plumbing company, I have attached an example of what I’m going for but want it to look better.

Target Market(s)

Home owners, real estate, etc.

Industry/Entity Type

Plumbing

Font styles to use
Other font styles liked:
• As per my logo and other examples uploaded

Colors

Designer to choose colors to be used in the design.

Requirements
Must have
• Must include my logo provided and similar to my flyer I have attached but better

```html
<!DOCTYPE html>
<html lang="en">
<head>
<meta charset="UTF-8">
<title>Brimlow Plumbing Solutions – Flyer</title>
<link rel="stylesheet" href="https://fonts.googleapis.com/css2?family=Montserrat:wght@600;700;800&family=Open+Sans:wght@400;500;600&display=swap">
<style>
  :root {
    --navy: #1b4d80;
    --navy-deep: #163f6a;
    --ink: #1a3f66;
    --stripe: #a9c6e0;
    --sky: #3f74a8;
    --paper: #ffffff;
    --backdrop: #e9eef3;
    --body-text: #1f2c3a;
  }
  * { margin: 0; padding: 0; box-sizing: border-box; }
  html, body {
    width: 1200px; height: 1200px; overflow: hidden;
    background: var(--backdrop);
  }
  .flyer {
    position: absolute; left: 102px; top: 60px;
    width: 995px; height: 1080px;
    background: var(--paper);
    font-family: "Open Sans", Arial, sans-serif;
    color: var(--body-text);
    box-shadow: 0 6px 24px rgba(20, 50, 90, .18);
    overflow: hidden;
  }
  .flyer-shapes { position: absolute; inset: 0; }
  .brand {
    position: absolute; left: 33px; top: 38px;
    display: flex; align-items: center; gap: 26px;
  }
  .brand-mark {
    width: 149px; height: 149px; border-radius: 50%;
    background: #d6e4f1; border: 5px solid var(--navy);
  }
  .brand-name {
    font-family: "Montserrat", Arial, sans-serif;
    font-weight: 800; color: var(--navy);
    font-size: 43px; line-height: 1.0; letter-spacing: .5px;
    text-transform: uppercase;
  }
  .brand-name .line-small { display: block; font-size: 31px; letter-spacing: 1px; margin-top: 4px; }
  .headline {
    position: absolute; left: 63px; top: 252px; width: 900px;
    font-family: "Montserrat", Arial, sans-serif;
    font-weight: 700; font-size: 44px; line-height: 52px;
    color: var(--paper); text-transform: uppercase; text-align: center;
  }
  .section-title {
    position: absolute;
    font-family: "Montserrat", Arial, sans-serif;
    font-weight: 700; font-size: 33px; color: var(--ink);
    text-decoration: underline; text-decoration-thickness: 3px; text-underline-offset: 6px;
  }
  .services-title { left: 45px; top: 444px; }
  .why-title { left: 375px; top: 620px; }
  .service-list { list-style: none; position: absolute; left: 45px; top: 0; }
  .service-list li {
    position: absolute; white-space: nowrap;
    font-size: 25px; line-height: 30px; padding-left: 22px;
  }
  .service-list li::before {
    content: ""; position: absolute; left: 2px; top: 12px;
    width: 7px; height: 7px; border-radius: 50%; background: var(--body-text);
  }
  .why-list { list-style: none; }
  .why-list li {
    position: absolute; left: 414px; display: flex; align-items: center; gap: 14px;
    font-size: 24px; white-space: nowrap;
  }
  .why-list svg { width: 30px; height: 30px; }
  .cta {
    position: absolute; left: 0; top: 847px; width: 995px; height: 233px;
    text-align: center; color: var(--paper);
  }
  .cta-line {
    font-family: "Montserrat", Arial, sans-serif; font-weight: 700; font-size: 31px;
    text-transform: uppercase; margin-top: 30px;
    text-decoration: underline; text-decoration-thickness: 2px; text-underline-offset: 6px;
  }
  .cta-phone {
    font-family: "Montserrat", Arial, sans-serif; font-weight: 700;
    font-size: 62px; letter-spacing: 3px; margin-top: 6px; line-height: 76px;
  }
  .contact-row {
    position: absolute; top: 158px; left: 63px; right: 40px;
    display: flex; justify-content: space-between; font-size: 22px;
  }
  .contact-item { display: flex; align-items: center; gap: 10px; }
  .contact-dot { width: 28px; height: 28px; border-radius: 50%; background: var(--paper); }
</style>
</head>
<body>
<div class="flyer">
  <svg class="flyer-shapes" width="995" height="1080" viewBox="0 0 995 1080" aria-hidden="false">
    <defs>
      <linearGradient id="heroTone" x1="0" y1="0" x2="1" y2="1">
        <stop offset="0" stop-color="#1b4d80"/>
        <stop offset="0.55" stop-color="#2d6096"/>
        <stop offset="1" stop-color="#4a7db0"/>
      </linearGradient>
    </defs>
    <polygon fill="var(--navy)" points="541,0 995,0 995,556 434,556 274,383 0,383 0,228 440,228"/>
    <g role="img" aria-label="Illustration of a large water pipe and tap above a house silhouette in blue tones">
      <polygon fill="url(#heroTone)" points="541,0 995,0 995,556 560,556 500,228 440,228"/>
    </g>
    <polygon fill="var(--stripe)" points="24,389 280,389 446,565 995,565 995,583 438,583 268,405 24,405"/>
    <rect x="0" y="847" width="995" height="233" fill="var(--navy)"/>
  </svg>

  <div class="brand">
    <div class="brand-mark"></div>
    <div class="brand-name">Brimlow<br>Plumbing<span class="line-small">Solutions</span></div>
  </div>

  <h1 class="headline">Reliable Plumbing Services<br>for Your Home &amp; Business</h1>

  <h2 class="section-title services-title">Our Services</h2>
  <ul class="service-list">
    <li style="top:499px">Blocked Drains</li>
    <li style="top:536px">Leaky Pipes</li>
    <li style="top:573px">Hot Water Systems</li>
    <li style="top:644px">Toilet Repairs</li>
    <li style="top:716px">Gas Fitting</li>
    <li style="top:789px">General Maintenance</li>
  </ul>

  <h2 class="section-title why-title">Why Choose Us?</h2>
  <ul class="why-list">
    <li style="top:691px">
      <svg viewBox="0 0 30 30" fill="none" stroke="var(--ink)" stroke-width="2"><circle cx="15" cy="10" r="5"/><path d="M5 27c0-6 4-10 10-10s10 4 10 10"/></svg>
      Experienced Plumbers
    </li>
    <li style="top:734px">
      <svg viewBox="0 0 30 30" fill="none" stroke="var(--ink)" stroke-width="2"><circle cx="15" cy="15" r="11"/><path d="M15 8v7l5 3"/></svg>
      24/7 Emergency Service
    </li>
    <li style="top:778px">
      <svg viewBox="0 0 30 30" fill="none" stroke="var(--ink)" stroke-width="2"><circle cx="15" cy="15" r="11"/><path d="M10 15l4 4 7-8"/></svg>
      Satisfaction Guaranteed
    </li>
  </ul>

  <footer class="cta">
    <p class="cta-line">Call Today for a Free Quote!</p>
    <p class="cta-phone">020 555 0182</p>
    <div class="contact-row">
      <span class="contact-item"><span class="contact-dot"></span>www.brimlow.co</span>
      <span class="contact-item"><span class="contact-dot"></span>brimlow_plumb</span>
      <span class="contact-item"><span class="contact-dot"></span>brimlowing.com</span>
    </div>
  </footer>
</div>
</body>
</html>
```